New, modern business card for growing audiology practice

We need a new business card for our audiology practice. Our logo and website have recently changed (more modern) and we want our business cards to reflect this change.
We conduct hearing tests, perform earwax removals, and fit & dispense hearing aids to our patients. We are a family owned practice in which the owner is the one who works directly with the patient. I have attached logos in various formats to use, as well as two ideas I found on this website; as well as a scanned copy of our current logo. Good luck!

Industry/Entity Type

Business

Contact Information for Business Card

Company name: Tolvera Hearing Center
Provider name: Peter Wolstenby, Au.D. F/NSB
Phone number: (440) 683-5127
Address: 837 W. Lindell Ave. Fernbrook Falls, OH 44093
email: tolverahearing@postvane.com
website: tolverahearing.com

Colors
000000
aaaaaa
dbdbdb
cacaca
9bcb3c
afd23c
cadf82
b1b1b1

Requirements
Must have
• My card must include information in the "details" section. In the attached images, I found a few that I liked and I would like to model after - "brisky bouncin'" and "Sound Method Center".
• Must be horizontal.
• Must include logos provided. I uploaded them in various file formats and various ways.
• Must match logo font, if possible, if not, please get as close as you can.
Nice to have
• I really like the idea of having a color on one side with just the logo and company name and the contact information and provider name on the other side. I also really like the idea of having the main color dominating on the logo/company side with accent of that same color on the contact side of the card.
Should not have
• Must not be vertical.

```html
<!DOCTYPE html>
<html lang="en">
<head>
<meta charset="utf-8">
<title>Tolvera Hearing Center – Business Card</title>
<link rel="stylesheet" href="https://fonts.googleapis.com/css2?family=Lato:wght@300;400;700&display=swap">
<style>
  :root {
    --ink: #000000;
    --lime: #afd23c;
    --lime-deep: #9bcb3c;
    --paper: #f8f8f8;
    --text-light: #ffffff;
    --text-soft: #e4e4e4;
    --text-dark: #1f1f1f;
    --backdrop: #dbdbdb;
  }
  * { margin: 0; padding: 0; box-sizing: border-box; }
  html, body {
    width: 1200px;
    height: 900px;
    overflow: hidden;
    background: var(--backdrop);
    font-family: "Lato", sans-serif;
  }
  .canvas {
    position: relative;
    width: 1200px;
    height: 900px;
  }
  .card {
    position: absolute;
    overflow: hidden;
    box-shadow: 0 6px 18px rgba(0,0,0,0.18);
  }

  /* Contact side */
  .card--contact {
    left: 178px;
    top: 73px;
    width: 588px;
    height: 364px;
    background: var(--ink);
  }
  .card--contact .accent-band {
    position: absolute;
    top: 0;
    right: 0;
    width: 200px;
    height: 100%;
    background: var(--lime);
  }
  .provider {
    position: absolute;
    left: 31px;
    top: 46px;
  }
  .provider__name {
    font-weight: 700;
    font-size: 21px;
    letter-spacing: 0.3px;
    color: var(--lime);
    text-transform: uppercase;
    line-height: 1.1;
  }
  .provider__name .comma { color: var(--text-light); }
  .provider__credentials {
    font-size: 16px;
    font-weight: 300;
    color: var(--text-soft);
    line-height: 1.4;
    letter-spacing: 0.3px;
  }
  .contact-list {
    position: absolute;
    left: 31px;
    top: 195px;
    list-style: none;
    color: var(--text-light);
    font-size: 16px;
    line-height: 22px;
  }
  .contact-list li {
    display: flex;
    align-items: flex-start;
  }
  .contact-list .icon {
    width: 14px;
    height: 14px;
    margin: 4px 6px 0 0;
    flex: none;
  }
  .contact-list .address { margin-bottom: 16px; }

  /* Brand side */
  .card--brand {
    left: 388px;
    top: 505px;
    width: 567px;
    height: 352px;
    background: var(--paper);
  }
  .brand-lockup {
    position: absolute;
    left: 0;
    right: 0;
    top: 154px;
    display: flex;
    align-items: center;
    justify-content: center;
    gap: 10px;
  }
  .brand-lockup__dot {
    width: 22px;
    height: 22px;
    border-radius: 50%;
    background: var(--lime);
  }
  .brand-lockup__name {
    font-size: 29px;
    font-weight: 400;
    color: var(--text-dark);
    letter-spacing: 0.3px;
    text-transform: uppercase;
  }
  .brand-url {
    position: absolute;
    left: 0;
    right: 0;
    top: 285px;
    text-align: center;
    font-size: 15px;
    font-weight: 700;
    color: var(--text-dark);
  }
  .brand-url .domain { color: var(--lime-deep); }
</style>
</head>
<body>
<main class="canvas">

  <section class="card card--contact" aria-label="Contact side">
    <div class="accent-band"></div>
    <div class="provider">
      <p class="provider__name">Peter Wolstenby<span class="comma">,</span></p>
      <p class="provider__credentials">AU.D. F/NSB</p>
    </div>
    <ul class="contact-list">
      <li class="address">
        <svg class="icon" viewBox="0 0 14 14"><path d="M7 0.5a4.5 4.5 0 0 0-4.5 4.5c0 3.3 4.5 8.5 4.5 8.5s4.5-5.2 4.5-8.5A4.5 4.5 0 0 0 7 0.5zm0 6.3a1.8 1.8 0 1 1 0-3.6 1.8 1.8 0 0 1 0 3.6z" fill="#afd23c"/></svg>
        <span>837 W. Lindell<br>Ave. Fernbrook Falls, OH 44093</span>
      </li>
      <li>
        <svg class="icon" viewBox="0 0 14 14"><path d="M3 1l2.2 2.6-1.2 1.6c.9 1.8 2.3 3.2 4.1 4.1l1.6-1.2L12.3 10.3 11 12.6C6 12.2 1.8 8 1.4 3z" fill="#afd23c"/></svg>
        <span>(440) 683-5127</span>
      </li>
      <li>
        <svg class="icon" viewBox="0 0 14 14"><rect x="1" y="3" width="12" height="8" fill="#afd23c"/><path d="M1 3l6 4.5L13 3" stroke="#000" stroke-width="1" fill="none"/></svg>
        <span>tolverahearing@postvane.com</span>
      </li>
      <li>
        <svg class="icon" viewBox="0 0 14 14"><circle cx="7" cy="7" r="6" fill="#afd23c"/><path d="M1 7h12M7 1c-2.5 3-2.5 9 0 12M7 1c2.5 3 2.5 9 0 12" stroke="#000" stroke-width="0.8" fill="none"/></svg>
        <span>www.tolverahearing.com</span>
      </li>
    </ul>
  </section>

  <section class="card card--brand" aria-label="Brand side">
    <div class="brand-lockup">
      <span class="brand-lockup__dot"></span>
      <span class="brand-lockup__name">Tolvera Hearing Center</span>
    </div>
    <p class="brand-url">www.<span class="domain">tolverahearing</span>.com</p>
  </section>

</main>
</body>
</html>
```